Cocktail-Making Assistant App re-design

Ok boys and girls, here's the deal:
I have an android app which is almost complete, but needs a design overhaul.

The app is a standard cocktail-making assistant: gives you a list of cocktails and the ability to see which cocktail you can make out of those ingredients (drinks, fruit, etc) you have at home.

I've attached some general app flow, as well as detailed requirements/explanation presentation. Most of those things are just FYI, so that you know what it's about.

3 screens are the most important (main screen, cocktail view screen, ingredient view screen), meaning I will pick the design mostly based on ideas for those 3 things, with the fourth being a rather simple list (given on attached flow, third tier)
Some other screens are derived from that, with some minor changes on it, but you shouldn't care about that.

There are lots of other, non-explained things which I said nothing about only because they are (from design point of view) completely the same and would only make it seem more complicated.

I don't want to influence the colour scheme, but the app will be released under RedFig developer name (having a light colured red fig as a logo) so I suppose some brownish design, for example, will not really fit nicely. If you, however, have a killer which you are confident will prove me wrong, I'm looking forward to seeing it!

It should be a serious, elegant look (as opposed to cartoonish, but we are not aiming for a business look at all!), not cluttered with details, no clubbing themes, glitter and so on.

Test apk file available on request (Android 2.3+).

Edit: payment is now guaranteed
Also please note that currently, the favorite, "heart" button has a motion effect:
on click it flies out of the screen to the left (white heart) and comes back to the screen as a red heart. Take that into consideration, if it means anything to you.

Target Market(s)

Whoever you imagine would enjoy drinking cocktails

Industry/Entity Type

Business

Requirements
Must have
• Everything is said in the provided documentation - images say more than I could possibly write here.
Nice to have
• As said, most of the icons are a nice-to-have. Only those which are critically linked to the rest of the design must be provided. More details in the docs.
Should not have
• No cartoon look, No zillion colours

```html
<!DOCTYPE html>
<html lang="en">
<head>
<meta charset="utf-8">
<title>ShakerBook – app screens</title>
<link href="https://fonts.googleapis.com/css2?family=Roboto:wght@300;400;500&display=swap" rel="stylesheet">
<style>
  :root{
    --canvas:#eef2f5;
    --screen-top:#cfe6ee;
    --screen-mid:#6fa9c4;
    --screen-deep:#123a5e;
    --bar:#0d2a47;
    --accent:#2f9bd8;
    --accent-light:#5cc3ee;
    --tile:#ffffff;
    --tile-text:#3a8fc2;
    --ink:#3b4650;
    --muted:#9aa4ab;
    --row-line:#e3e7ea;
    --badge:#e6e8ea;
    --tick:#8cbf3f;
    --heart:#e2313a;
    --panel:#1f5f9a;
    --panel-row:#2a6ea9;
  }
  *{box-sizing:border-box;margin:0;padding:0}
  html,body{width:1200px;height:720px;overflow:hidden}
  body{background:var(--canvas);font-family:"Roboto",Arial,sans-serif;font-weight:300;position:relative}
  .screen{position:absolute;top:195px;width:232px;height:312px;overflow:hidden;border-radius:3px;
    background:linear-gradient(180deg,var(--screen-top) 0%,var(--screen-mid) 45%,var(--screen-deep) 100%);
    box-shadow:0 6px 20px rgba(0,0,0,.18)}
  .screen--home{left:133px}
  .screen--ingredient{left:485px}
  .screen--cocktail{left:838px}

  /* home */
  .home-title{position:absolute;top:14px;left:0;width:100%;text-align:center;font-size:14px;font-weight:300;color:var(--ink)}
  .tile{position:absolute;width:95px;height:66px;background:var(--tile);border-radius:2px;
    box-shadow:0 1px 3px rgba(0,0,0,.2);text-align:center}
  .tile__icon{display:block;margin:7px auto 0;width:34px;height:32px;border-radius:4px}
  .tile__label{position:absolute;left:0;right:0;bottom:5px;display:block;text-align:center;font-size:11.5px;line-height:14px;color:var(--tile-text);white-space:nowrap}
  .col-a{left:14px}.col-b{left:119px}
  .row-1{top:42px}.row-2{top:120px}.row-3{top:197px}
  .bottom-bar{position:absolute;left:0;bottom:0;width:100%;height:34px;background:var(--bar)}
  .points{position:absolute;left:18px;top:9px;font-size:13px;color:#fff}
  .points small{font-size:9px;color:var(--accent-light)}
  .settings-btn{position:absolute;right:12px;top:8px;width:24px;height:18px;border-radius:2px;background:var(--accent)}

  /* ingredient */
  .dim{position:absolute;inset:0;background:rgba(8,30,55,.55)}
  .top-bar{position:absolute;top:0;left:0;width:100%;height:34px;background:#0f3457}
  .top-bar__title{position:absolute;left:0;width:100%;text-align:center;top:9px;font-size:13px;color:#7f95aa}
  .info-card{position:absolute;left:8px;top:48px;width:138px;height:60px;background:#15385a;border-radius:2px;padding:7px 9px;color:#8ea3b6;font-size:10px;line-height:13px}
  .info-card strong{display:block;font-weight:400;font-size:11px;margin-bottom:3px;white-space:nowrap}
  .info-photo{position:absolute;left:156px;top:48px;width:66px;height:60px;border-radius:2px;background:linear-gradient(160deg,#5b6f82,#2d4258)}
  .info-card--lower{top:122px;height:30px}
  .similar-tab{position:absolute;left:58px;top:112px;width:116px;height:22px;background:var(--accent);border-radius:6px 6px 0 0;
    text-align:center;font-size:9px;color:#d7eefa;padding-top:4px;white-space:nowrap}
  .similar-tab b{font-weight:500;color:#fff;font-size:10px}
  .similar-panel{position:absolute;left:8px;right:8px;top:132px;bottom:0;background:var(--panel);border-radius:2px}
  .similar-row{height:29px;border-bottom:1px solid #1a4f80;text-align:center;color:#fff;font-size:13.5px;line-height:29px;background:var(--panel-row)}
  .similar-row:last-child{opacity:.35}

  /* cocktail */
  .cocktail-bar{position:absolute;top:4px;left:0;width:100%;height:32px;background:var(--accent-light)}
  .cocktail-bar__title{position:absolute;left:38px;right:36px;top:0;height:32px;background:#e8f6fc;
    text-align:center;line-height:32px;font-size:13px;color:var(--accent);white-space:nowrap}
  .cocktail-bar svg{position:absolute;top:8px}
  .stars{position:absolute;left:20px;top:54px}
  .drink-photo{position:absolute;left:160px;top:50px;width:62px;height:62px;border-radius:2px;
    background:radial-gradient(circle at 50% 55%,#3cd27a 0%,#1b7f4b 35%,#2a2f33 80%)}
  .fav-btn{position:absolute;left:12px;top:90px;width:34px;height:22px;border-radius:2px;background:#dff0f8;border:1px solid var(--accent)}
  .fav-btn svg{position:absolute;left:7px;top:2px}
  .vol-btn{position:absolute;left:50px;top:90px;width:100px;height:22px;border-radius:2px;background:#1b6fae;color:#d6eefb;font-size:10px;line-height:22px;padding-left:20px;white-space:nowrap}
  .ingredients{position:absolute;left:10px;top:124px;width:212px;height:138px;background:#fff;border-radius:2px;overflow:hidden}
  .ingredient{position:relative;height:29px;border-bottom:1px solid var(--row-line);font-size:12px;color:var(--ink);line-height:29px;padding-left:46px;white-space:nowrap}
  .ingredient small{font-size:8px;color:var(--muted)}
  .amount{position:absolute;left:5px;top:6px;width:32px;height:17px;background:var(--badge);border-radius:2px;font-size:8.5px;color:#6b757c;line-height:17px;text-align:center}
  .ingredient svg{position:absolute;right:10px;top:7px}
  .ingredient--faded{opacity:.35}
  .detail-tab{position:absolute;left:70px;bottom:6px;width:94px;height:22px;background:#1d5b8e;border-radius:6px 6px 0 0;color:#bfe3f6;font-size:9px;line-height:22px;text-align:center;white-space:nowrap}
  .detail-tab b{font-style:italic;font-weight:500;color:#fff;font-size:12px;margin-right:4px}
</style>
</head>
<body>

<section class="screen screen--home" aria-label="Home screen">
  <h1 class="home-title">Welcome to ShakerBook</h1>
  <div class="tile col-a row-1"><span class="tile__icon" role="img" aria-label="Cocktail shaker icon" style="background:linear-gradient(180deg,#c9ced3,#6d747a)"></span><span class="tile__label">Shaker</span></div>
  <div class="tile col-b row-1"><span class="tile__icon" role="img" aria-label="Row of liquor bottles icon" style="width:54px;background:linear-gradient(90deg,#c57a2a,#7a3d1a,#c9a040,#8b2f2f)"></span><span class="tile__label">My Bar</span></div>
  <div class="tile col-a row-2"><span class="tile__icon" role="img" aria-label="Two colourful cocktail glasses icon" style="background:linear-gradient(160deg,#f5b12a,#e4572e)"></span><span class="tile__label">Cocktails</span></div>
  <div class="tile col-b row-2"><svg class="tile__icon" viewBox="0 0 34 32" aria-hidden="true"><path d="M17 29 C5 20 2 14 4 9 C6 4 13 3 17 9 C21 3 28 4 30 9 C32 14 29 20 17 29Z" fill="var(--heart)"/></svg><span class="tile__label">Favorites</span></div>
  <div class="tile col-a row-3"><span class="tile__icon" role="img" aria-label="Shopping basket icon" style="background:linear-gradient(180deg,#7cc7ef,#2a86c6)"></span><span class="tile__label">Shopping List</span></div>
  <div class="tile col-b row-3"><span class="tile__icon" role="img" aria-label="Award ribbon icon" style="width:24px;background:linear-gradient(180deg,#e8b94a,#a86f1c)"></span><span class="tile__label">Featured</span></div>
  <div class="bottom-bar">
    <span class="points">100 <small>Points</small></span>
    <span class="settings-btn"><svg width="24" height="18" viewBox="0 0 24 18" aria-hidden="true"><circle cx="11" cy="10" r="4" fill="none" stroke="#fff" stroke-width="2"/><circle cx="16.5" cy="5.5" r="2" fill="none" stroke="#fff" stroke-width="1.2"/></svg></span>
  </div>
</section>

<section class="screen screen--ingredient" aria-label="Ingredient screen with similar ingredients">
  <div class="top-bar"><span class="top-bar__title">Description</span></div>
  <div class="info-card"><strong>Dunmore's Irish Cream</strong>Type: Liqueur / Cordial<br>Alc: 17.00%</div>
  <div class="info-photo" role="img" aria-label="Photo of cream liqueur bottles"></div>
  <div class="info-card info-card--lower">Description</div>
  <div class="dim"></div>
  <div class="similar-tab"><b>12</b> Similar Ingredients</div>
  <div class="similar-panel">
    <div class="similar-row">Palmera Rum</div>
    <div class="similar-row">Light Rum</div>
    <div class="similar-row">151 Proof Rum</div>
    <div class="similar-row">Dark Creme de Cacao</div>
    <div class="similar-row">Milk</div>
    <div class="similar-row">Orange Juice</div>
  </div>
</section>

<section class="screen screen--cocktail" aria-label="Cocktail screen">
  <div class="cocktail-bar">
    <svg style="left:12px" width="16" height="16" viewBox="0 0 16 16" aria-hidden="true"><path d="M14 8H3M8 3L3 8l5 5" stroke="#fff" stroke-width="2.2" fill="none"/></svg>
    <div class="cocktail-bar__title">151 Florida Bushwack</div>
    <svg style="right:9px" width="20" height="16" viewBox="0 0 20 16" aria-hidden="true"><rect x="1" y="3" width="18" height="12" rx="2" fill="none" stroke="#fff" stroke-width="1.6"/><circle cx="10" cy="9" r="3.5" fill="none" stroke="#fff" stroke-width="1.6"/></svg>
  </div>
  <svg class="stars" width="120" height="20" viewBox="0 0 120 20" aria-label="Rated 4 of 5">
    <defs><path id="star" d="M10 1l2.6 6 6.4.5-4.9 4.2 1.5 6.3L10 14.6 4.4 18l1.5-6.3L1 7.5l6.4-.5z"/></defs>
    <use href="#star" fill="#fff"/><use href="#star" x="24" fill="#fff"/><use href="#star" x="48" fill="#fff"/><use href="#star" x="72" fill="#fff"/><use href="#star" x="96" fill="none" stroke="#fff" stroke-width="1.2"/>
  </svg>
  <div class="drink-photo" role="img" aria-label="Photo of a green layered cocktail in a glass"></div>
  <div class="fav-btn"><svg width="18" height="16" viewBox="0 0 34 32" aria-hidden="true"><path d="M17 29 C5 20 2 14 4 9 C6 4 13 3 17 9 C21 3 28 4 30 9 C32 14 29 20 17 29Z" fill="var(--heart)"/></svg></div>
  <div class="vol-btn">Vol. Unavailable</div>
  <div class="ingredients">
    <div class="ingredient"><span class="amount">½ OZ</span>Palmera Rum<svg width="16" height="14" viewBox="0 0 16 14" aria-hidden="true"><path d="M1 7l5 5L15 1" stroke="var(--tick)" stroke-width="2.2" fill="none"/></svg></div>
    <div class="ingredient"><span class="amount">½ OZ</span>Light Rum<svg width="16" height="14" viewBox="0 0 16 14" aria-hidden="true"><path d="M1 2h3l2 7h8l1-5H5" stroke="#b8c0c6" stroke-width="1.4" fill="none"/><circle cx="7" cy="12" r="1.2" fill="#b8c0c6"/><circle cx="13" cy="12" r="1.2" fill="#b8c0c6"/></svg></div>
    <div class="ingredient"><span class="amount">1 OZ</span>151 Proof Rum <small>(Bravado)</small><svg width="16" height="14" viewBox="0 0 16 14" aria-hidden="true"><path d="M1 2h3l2 7h8l1-5H5" stroke="#b8c0c6" stroke-width="1.4" fill="none"/><path d="M9 5l2 2 4-4" stroke="var(--tick)" stroke-width="1.6" fill="none"/></svg></div>
    <div class="ingredient"><span class="amount">1 OZ</span>Dark Creme de Cacao<svg width="16" height="14" viewBox="0 0 16 14" aria-hidden="true"><path d="M1 7l5 5L15 1" stroke="var(--tick)" stroke-width="2.2" fill="none"/></svg></div>
    <div class="ingredient ingredient--faded"><span class="amount">2 OZ</span>Milk<svg width="16" height="14" viewBox="0 0 16 14" aria-hidden="true"><path d="M1 2h3l2 7h8l1-5H5" stroke="#b8c0c6" stroke-width="1.4" fill="none"/></svg></div>
  </div>
  <div class="bottom-bar" style="height:44px"></div>
  <div class="detail-tab"><b>i</b>Description</div>
</section>

</body>
</html>
```